New website: Wanderfjordia.com

We need to build a website for our small travel agency.
We want to be able to upload our brochures and offer our tours on site. No online payments involved yet.

We want to create an exact copy of another website: www.trekvalora.is, but with our own information and products. We like that design very much.

We are not going to do any sales via the website as the website above, but instead we want to show in the same style and everything the different tours that we offer.

We need to be able to modify tours: tour pictures, info, add videos, text, etc.

We need the website in English and Spanish. We can provide the Spanish translation.

We would advice you to create a copy of that website, with the text to be editable by us.
We own the website www.wanderfjordia.com and need that the designer uploads it and makes it work as well.

We have uploaded some pictures that can be used as place markers.

I HAVE UPLOADED OUR BROCHURE DEMO SO YOU CAN GET MORE INFO IN ENGLISH ABOUT US AND MORE PICTURES.

PLEASE REMEMBER THAT THE WEBSITE ¨MOVES¨ when you resize it! Specially the pictures get ¨bigger¨ or smaller¨ when you resize. The same applies to the logos :-)

Once you have created the front page just as the original website I will select it and then we can put the real info and extra pages :-)

Tourists, international people traveling.

Tourism

Coded - Design and coding required

5+ page

Sans Serif

ffffff

• Exactly the same layout of the website mentioned (www.trekvalora.is)
• Everything the same, but with our own logo, texts and photos.
• HOME
• TOURS
• GROUPS
• OUR MOST POPULAR TOURS

```html
<!DOCTYPE html>
<html lang="es">
<head>
<meta charset="utf-8">
<title>Wanderfjordia</title>
<link rel="stylesheet" href="https://fonts.googleapis.com/css2?family=Open+Sans:ital,wght@0,300;0,400;0,600;1,700&display=swap">
<style>
  :root {
    --red: #e4161b;
    --ink: #1b1b1b;
    --text: #3a3a3a;
    --muted: #8a8a8a;
    --white: #ffffff;
    --footer: #ececec;
    --line: #c9c9c9;
  }
  * { margin: 0; padding: 0; box-sizing: border-box; }
  html, body { width: 1200px; height: 3279px; overflow: hidden; }
  body { position: relative; background: var(--white); font-family: "Open Sans", Arial, sans-serif; color: var(--text); }
  .abs { position: absolute; }

  /* header */
  .site-header { top: 0; left: 0; width: 1200px; height: 151px; background: var(--white); }
  .brand { display: flex; align-items: center; gap: 12px; }
  .brand-dot { width: 44px; height: 44px; border-radius: 50%; background: var(--ink); }
  .brand-name { font-size: 26px; font-weight: 600; color: var(--ink); }
  .site-header .brand { left: 164px; top: 57px; }
  .lang { left: 953px; top: 34px; font-size: 9px; letter-spacing: .5px; color: var(--text); display: flex; align-items: center; gap: 6px; }
  .lang-flag { width: 24px; height: 14px; background: linear-gradient(#b22234 0 15%, #fff 15% 30%, #b22234 30% 45%, #fff 45% 60%, #b22234 60% 75%, #fff 75% 90%, #b22234 90%); position: relative; }
  .lang-flag::before { content: ""; position: absolute; left: 0; top: 0; width: 10px; height: 8px; background: #3c3b6e; }
  .main-nav { top: 86px; left: 0; width: 1200px; }
  .main-nav a { position: absolute; transform: translateX(-50%); font-size: 17px; color: var(--text); text-decoration: none; white-space: nowrap; }
  .main-nav a.active { color: var(--ink); }
  .nav-underline { left: 478px; top: 119px; width: 62px; height: 4px; background: var(--red); }

  /* hero */
  .hero { top: 151px; left: 0; width: 1200px; height: 562px;
    background: linear-gradient(180deg, #6f9bcf 0%, #a9bfd8 22%, #8c96a3 42%, #5d6570 58%, #3b4650 72%, #2a2e30 86%, #1d1f20 100%); }
  .hero-title { top: 320px; width: 1200px; text-align: center; font-size: 42px; font-weight: 300; color: var(--white); letter-spacing: 1px; }
  .hero-dots { top: 514px; left: 556px; display: flex; gap: 12px; }
  .hero-dots span { width: 12px; height: 12px; border-radius: 50%; background: var(--white); }
  .hero-dots span.on { background: var(--red); }

  /* sections */
  .section-title { font-size: 47px; font-weight: 300; color: var(--ink); letter-spacing: 1px; line-height: 1; white-space: nowrap; }
  .section-title .accent { color: var(--red); }
  .centered { left: 0; width: 1200px; text-align: center; }
  .lead { font-size: 13.5px; line-height: 1.95; color: var(--text); }
  .shadow-band { left: 140px; width: 920px; height: 40px; background: radial-gradient(ellipse at 50% 0%, rgba(0,0,0,.09), rgba(0,0,0,0) 70%); }

  .welcome-title { top: 768px; }
  .welcome-text { top: 842px; left: 150px; width: 900px; text-align: center; }

  .about-title { top: 1066px; left: 140px; }
  .about-text { top: 1158px; left: 144px; width: 500px; }
  .photo-circle { width: 364px; height: 364px; border-radius: 50%; border: 6px solid var(--red); overflow: hidden; }
  .about-photo { left: 692px; top: 1001px; background: linear-gradient(180deg, #5a86bd 0%, #9db7d6 38%, #d7dde3 52%, #4d7fa6 60%, #2f8fb1 78%, #1e6f91 100%); }

  .mission { top: 1449px; left: 0; width: 1200px; height: 394px;
    background: linear-gradient(180deg, #4a4e53 0%, #393c40 40%, #26292c 75%, #1d1f21 100%); }
  .mission-title { top: 125px; color: var(--white); }
  .mission-text { top: 189px; left: 150px; width: 900px; text-align: center; color: #e6e6e6; }

  .vision-title { top: 1950px; left: 144px; }
  .vision-text { top: 2024px; left: 144px; width: 490px; }
  .signatures { left: 144px; top: 2186px; width: 260px; height: 74px; background: linear-gradient(90deg, rgba(0,0,0,0), rgba(0,0,0,.04), rgba(0,0,0,0)); }
  .signature-caption { left: 204px; top: 2264px; font-size: 11px; color: var(--text); }
  .vision-photo { left: 692px; top: 1925px; background: radial-gradient(circle at 50% 60%, #7a7468 0%, #a3894c 45%, #c9a23e 75%, #8e7a34 100%); }
  .vision-caption { left: 0; top: 168px; width: 352px; text-align: center; color: var(--white); font-size: 24px; font-weight: 400; line-height: 1.2; }

  .tours-title { top: 2390px; }
  .tour-card { top: 2536px; width: 289px; }
  .tour-photo { width: 289px; height: 199px; border: 6px solid var(--red); }
  .tour-photo.one { background: linear-gradient(180deg, #3c6fb5 0%, #8fb1d8 35%, #e6edf4 50%, #6f7f6c 66%, #a89a5a 100%); }
  .tour-photo.two { background: linear-gradient(180deg, #8d8f93 0%, #c3c5c8 30%, #5e6167 55%, #4f8a9b 72%, #3f4a3f 100%); }
  .tour-photo.three { background: linear-gradient(180deg, #b8cde0 0%, #e7eef5 30%, #7f95ab 55%, #566a7e 78%, #3b4652 100%); }
  .tour-name { margin-top: 44px; font-size: 18px; font-weight: 700; font-style: italic; color: var(--ink); }
  .tour-text { margin-top: 18px; font-size: 12.5px; line-height: 1.75; color: var(--muted); }

  /* footer */
  .site-footer { left: 0; top: 2956px; width: 1200px; height: 323px; background: var(--footer); }
  .site-footer .brand { position: absolute; top: 66px; left: 0; width: 1200px; justify-content: center; }
  .social { top: 176px; left: 0; width: 1200px; display: flex; justify-content: center; gap: 12px; }
  .social span { width: 14px; height: 14px; border-radius: 50%; background: #333; }
  .footer-nav { top: 210px; left: 0; width: 1200px; text-align: center; font-size: 13px; color: var(--text); }
  .footer-nav span { margin: 0 12px; }
  .footer-nav i { font-style: normal; color: #666; }
  .copyright { top: 248px; left: 0; width: 1200px; text-align: center; font-size: 12.5px; color: var(--text); }
</style>
</head>
<body>

<header class="site-header abs">
  <div class="brand abs"><span class="brand-dot"></span><span class="brand-name">Wanderfjordia</span></div>
  <div class="lang abs">LANGUAGES <span class="lang-flag"></span></div>
  <nav class="main-nav abs">
    <a class="active" style="left:509px">HOME</a>
    <a style="left:595px">TOURS</a>
    <a style="left:695px">GROUPS</a>
    <a style="left:798px">RENT A CAR</a>
    <a style="left:912px">FLIGHT</a>
    <a style="left:1010px">CONTACT</a>
  </nav>
  <div class="nav-underline abs"></div>
</header>

<section class="hero abs" role="img" aria-label="Photo of snowy granite peaks above a lake with travellers in the foreground">
  <h1 class="hero-title abs">WANDERFJORDIA</h1>
  <div class="hero-dots abs"><span class="on"></span><span></span><span></span><span></span></div>
</section>

<h2 class="section-title welcome-title centered abs">WELCOME TO WANDERFJORDIA</h2>
<p class="lead welcome-text abs">Wanderfjordia es un nuevo tour operator receptivo de confianza especializado en el diseño y prestación de servicios personalizados de incoming en destinos prístinos de la Ecorregión Sub-Antártica y Antártica Chilena.</p>
<div class="shadow-band abs" style="top:938px"></div>

<h2 class="section-title about-title abs"><span class="accent">QUIENES</span> SOMOS</h2>
<p class="lead about-text abs">Somos una empresa conformada por un idóneo equipo de trabajo que consta de alta motivación, óptimo entrenamiento, elevado capital humano y cuyos integrantes poseen más de 10 años de experiencia trabajando en forma independiente en Turismo Receptivo Regional, Nacional e Internacional. En conjunto nos potenciamos y logramos satisfacer las altas demandas de servicios turísticos requeridos por nuestros clientes.</p>
<div class="photo-circle about-photo abs" role="img" aria-label="Photo of a lakeside lodge with snow-capped mountains behind"></div>

<section class="mission abs" role="img" aria-label="Dark photo of a mountain range under cloud">
  <h2 class="section-title mission-title centered abs">MISION</h2>
  <p class="lead mission-text abs">Nuestra misión es ofrecer servicios de Turismo Receptivo para la Región de Magallanes y Antártica Chilena que cumplan con las exigencias de calidad y valor humano que nuestros clientes solicitan. Para lograrlo, trabajamos en conjunto con proveedores turísticos seleccionados y nos enfocamos hacia la excelencia de un servicio personalizado, sirviendo con pasión, experiencia y responsabilidad a cada uno de nuestros clientes.</p>
</section>

<h2 class="section-title vision-title abs">VISION</h2>
<p class="lead vision-text abs">Nuestra visión es crear una Plataforma de Servicios Logísticos y Turísticos para la Ecorregión Sub-Antártica y Antártica que una toda la oferta turística de la zona a través de una red local, nacional y global de proveedores, con el objetivo de mejorar, a través de la cuidadosa selección de prestadores, la accesibilidad por parte del cliente, la competitividad dentro del mercado, facilitando la inclusión de pequeñas y medianas empresas.</p>
<div class="signatures abs" role="img" aria-label="Handwritten signatures of the team"></div>
<p class="signature-caption abs">Equipo Wanderfjordia</p>
<div class="photo-circle vision-photo abs" role="img" aria-label="Photo of a smiling team member outdoors">
  <p class="vision-caption abs">SALUDOS<br>CORDIALES</p>
</div>

<h2 class="section-title tours-title centered abs">OUR TOURS</h2>
<div class="shadow-band abs" style="top:2478px"></div>

<article class="tour-card abs" style="left:144px">
  <div class="tour-photo one" role="img" aria-label="Photo of jagged peaks above a grassy valley road"></div>
  <h3 class="tour-name">Patagonia</h3>
  <p class="tour-text">At vero eos et accusamus et iusto odio dignissimos ducimus qui blanditiis praesentium voluptatum deleniti atque corrupti</p>
</article>
<article class="tour-card abs" style="left:455px">
  <div class="tour-photo two" role="img" aria-label="Photo of rocky mountains over a glacial lake"></div>
  <h3 class="tour-name">Patagonia</h3>
  <p class="tour-text">At vero eos et accusamus et iusto odio dignissimos ducimus qui blanditiis praesentium voluptatum deleniti atque corrupti</p>
</article>
<article class="tour-card abs" style="left:767px">
  <div class="tour-photo three" role="img" aria-label="Photo of a hiker facing snowy mountain slopes"></div>
  <h3 class="tour-name">Patagonia</h3>
  <p class="tour-text">At vero eos et accusamus et iusto odio dignissimos ducimus qui blanditiis praesentium voluptatum deleniti atque corrupti</p>
</article>

<footer class="site-footer abs">
  <div class="brand"><span class="brand-dot"></span><span class="brand-name">Wanderfjordia</span></div>
  <div class="social abs"><span></span><span></span><span></span><span></span><span></span><span></span></div>
  <nav class="footer-nav abs">
    <span>HOME</span><i>|</i><span>TOURS</span><i>|</i><span>GROUPS</span><i>|</i><span>RENT A CAR</span><i>|</i><span>FLIGHT</span><i>|</i><span>CONTACT</span>
  </nav>
  <p class="copyright abs">© 2016 COMPANY NAME | ALL RIGHTS RESERVED</p>
</footer>
</body>
</html>
```